Dynamic Business Card for Sports Supplements Company

Hi! I'm looking for an awesome business card to match my existing sports supplement company. I have uploaded my current company logo and screenshot of the front page of my website.

I would like to have something dynamic and interesting and utilize the colors in the website - the reds and purples

The business card should be double sided and focus on a unique eye-catching design on the back and include all the relevant company info.

Most importantly, it should say somewhere: "Sign up on our website for a coupon code."

Target Market(s)

Mostly for women gym goers but it shouldn't be too feminine. It should be in keeping with the website design. It should flow and clearly be connected to it

Industry/Entity Type

Business

Contact Information for Business Card

Lorraine K. Vestal
CEO
LVestal@Quorvanexco.com
www.quorvanexco.com
555.417.3820
P.O. Box 47315
Halden, Vermont 00000

Sign up on our website for a coupon code

Font styles to use
Serif
Sans Serif
Other font styles liked:
• Novecento font family and "Quorvanex" is in AR Destine font

Requirements
Must have
• One side should be a bold Quorvanex logo design. Even just the symbol itself may be o.k. (see attached file)

```html
<!DOCTYPE html>
<html lang="en">
<head>
<meta charset="utf-8">
<title>Quorvanex Business Card</title>
<link href="https://fonts.googleapis.com/css2?family=Montserrat:wght@400;500;600;800&display=swap" rel="stylesheet">
<style>
  :root {
    --bg: #3b3b3d;
    --card: #ffffff;
    --ink: #111111;
    --black: #050505;
    --red: #e3222b;
    --white: #ffffff;
  }
  * { box-sizing: border-box; margin: 0; padding: 0; }
  html, body { width: 1200px; height: 855px; overflow: hidden; }
  body {
    background: var(--bg);
    font-family: "Montserrat", Arial, sans-serif;
    position: relative;
  }
  .card {
    position: absolute;
    left: 354px;
    width: 493px;
    background: var(--card);
    box-shadow: 0 6px 18px rgba(0,0,0,0.45);
    overflow: hidden;
  }
  /* Front side */
  .card-front { top: 137px; height: 280px; }
  .front-mark {
    position: absolute;
    left: 50%;
    top: 62px;
    transform: translateX(-50%);
    display: flex;
    flex-direction: column;
    align-items: center;
    gap: 12px;
  }
  .front-ring {
    width: 90px; height: 90px;
    border: 6px solid var(--ink);
    border-radius: 50%;
  }
  .front-name {
    font-weight: 800;
    font-size: 22px;
    letter-spacing: 1px;
    color: var(--ink);
    text-transform: uppercase;
    line-height: 1;
  }
  .coupon-note {
    position: absolute;
    left: 0; right: 0;
    top: 240px;
    text-align: center;
    font-size: 13px;
    color: var(--ink);
  }
  /* Back side */
  .card-back { top: 430px; height: 288px; }
  .back-shape { position: absolute; inset: 0; }
  .contact {
    position: absolute;
    left: 26px;
    top: 118px;
    color: var(--white);
  }
  .contact-name { color: var(--red); font-size: 18px; font-weight: 500; line-height: 1.1; }
  .contact-role { font-size: 13px; margin-top: 2px; }
  .contact-address { font-size: 13px; line-height: 17px; margin-top: 12px; }
  .contact-lines { list-style: none; font-size: 13px; line-height: 17px; margin-top: 11px; }
  .contact-lines li { display: flex; align-items: center; gap: 5px; }
  .contact-lines svg { width: 11px; height: 11px; flex: none; }
  .brand {
    position: absolute;
    left: 300px;
    width: 170px;
    top: 30px;
    display: flex;
    flex-direction: column;
    align-items: center;
  }
  .brand-dot {
    width: 46px; height: 46px;
    border-radius: 50%;
    background: var(--red);
    margin-bottom: 12px;
  }
  .brand-name {
    font-weight: 800;
    font-size: 22px;
    letter-spacing: 1px;
    color: var(--ink);
    text-transform: uppercase;
    line-height: 1;
  }
  .brand-tagline {
    font-size: 8.5px;
    letter-spacing: 0.6px;
    color: var(--ink);
    text-transform: uppercase;
    margin-top: 4px;
    white-space: nowrap;
  }
</style>
</head>
<body>
  <section class="card card-front">
    <div class="front-mark">
      <div class="front-ring"></div>
      <div class="front-name">Quorvanex</div>
    </div>
    <p class="coupon-note">Sign up on our website for a coupon code</p>
  </section>

  <section class="card card-back">
    <svg class="back-shape" width="493" height="288" viewBox="0 0 493 288">
      <polygon points="0,0 167,0 317,288 0,288" fill="var(--black)"/>
      <line x1="172" y1="0" x2="322" y2="288" stroke="var(--red)" stroke-width="3.5"/>
    </svg>

    <div class="contact">
      <p class="contact-name">Lorraine K. Vestal</p>
      <p class="contact-role">CEO</p>
      <p class="contact-address">P.O. Box 47315<br>Halden, Vermont 00000</p>
      <ul class="contact-lines">
        <li>
          <svg viewBox="0 0 12 12" aria-hidden="true"><path d="M3 1 L5 3 L4 4.5 Q5 7 7.5 8 L9 7 L11 9 L9.5 11 Q2 10 1 2.5 Z" fill="var(--red)"/></svg>
          555.417.3820
        </li>
        <li>
          <svg viewBox="0 0 12 12" aria-hidden="true"><rect x="0.5" y="2.5" width="11" height="7.5" fill="var(--red)"/><path d="M0.5 2.5 L6 7 L11.5 2.5" stroke="var(--black)" stroke-width="1" fill="none"/></svg>
          LVestal@Quorvanexco.com
        </li>
        <li>
          <svg viewBox="0 0 12 12" aria-hidden="true" fill="none" stroke="var(--red)" stroke-width="1"><circle cx="6" cy="6" r="5"/><ellipse cx="6" cy="6" rx="2.2" ry="5"/><line x1="1" y1="6" x2="11" y2="6"/></svg>
          www.quorvanexco.com
        </li>
      </ul>
    </div>

    <div class="brand">
      <div class="brand-dot"></div>
      <div class="brand-name">Quorvanex</div>
      <div class="brand-tagline">Strength In Every Scoop</div>
    </div>
  </section>
</body>
</html>
```